Dr. Quill Enterprises
Business card, stationary, fax page, envelope
Dr. Quill Enterprises - Corporate Services
Creative Brief
Bright & Fun-filled
Derek Spanning Oberwald
Senior Account Executive
417 W. Pellham Ave Los Angeles CA 90027
derek@drquillenterprises.com
drquillenterprises.com
I also have 4 other people that need their won business cards but with their cell phone and title info.

```html
<!DOCTYPE html>
<html lang="en">
<head>
<meta charset="utf-8">
<title>Dr. Quill Enterprises – Business Card</title>
<link href="https://fonts.googleapis.com/css2?family=Open+Sans:wght@400;600;700;800&display=swap" rel="stylesheet">
<style>
  :root {
    --backdrop: #e9e5df;
    --card: #ffffff;
    --ink: #2b2b2b;
    --accent: #c4672b;
    --copper-light: #f2b98f;
    --band-dark: #141414;
    --logo-grey: #6b6b6b;
  }
  * { margin: 0; padding: 0; box-sizing: border-box; }
  html, body {
    width: 1200px; height: 965px; overflow: hidden;
    background: var(--backdrop);
    font-family: "Open Sans", Arial, sans-serif;
    color: var(--ink);
  }
  .business-card {
    position: absolute; left: 100px; top: 188px;
    width: 1000px; height: 588px;
    background: var(--card);
    border-radius: 28px;
    overflow: hidden;
    box-shadow: 0 10px 30px rgba(0,0,0,.18);
  }
  .brand { position: absolute; left: 236px; top: 60px; display: flex; align-items: center; gap: 28px; }
  .brand-dot { width: 120px; height: 120px; border-radius: 50%; background: var(--copper-light); }
  .brand-name {
    font-weight: 800; font-size: 58px; line-height: 1.02; color: var(--logo-grey);
    letter-spacing: -0.5px;
  }
  .person { position: absolute; right: 491px; top: 290px; text-align: right; white-space: nowrap; }
  .person-name { font-weight: 700; font-size: 32px; color: var(--accent); line-height: 1.2; }
  .person-title { font-weight: 700; font-size: 21px; margin-top: 4px; }
  .person-address { font-size: 21px; line-height: 32px; margin-top: 18px; }
  .divider { position: absolute; left: 524px; top: 280px; width: 3px; height: 205px; background: var(--accent); }
  .contact-list { position: absolute; left: 548px; top: 281px; list-style: none; }
  .contact-item { display: flex; align-items: center; height: 41px; font-size: 22px; white-space: nowrap; }
  .contact-icon { width: 24px; height: 24px; margin-right: 18px; flex: none; }
  .contact-icon * { fill: var(--accent); }
  .footer-band { position: absolute; left: 0; bottom: 0; width: 1000px; height: 57px; }
</style>
</head>
<body>
<div class="business-card">
  <div class="brand">
    <div class="brand-dot"></div>
    <div class="brand-name">Dr. Quill<br>Enterprises</div>
  </div>

  <div class="person">
    <div class="person-name">Derek Spanning Oberwald</div>
    <div class="person-title">Senior Account Executive</div>
    <div class="person-address">417 W. Pellham Ave<br>Los Angeles CA 90027</div>
  </div>

  <div class="divider"></div>

  <ul class="contact-list">
    <li class="contact-item">
      <svg class="contact-icon" viewBox="0 0 24 24"><path d="M6.6 10.8a15 15 0 0 0 6.6 6.6l2.2-2.2a1 1 0 0 1 1-.25 11.4 11.4 0 0 0 3.6.57 1 1 0 0 1 1 1V20a1 1 0 0 1-1 1A17 17 0 0 1 3 4a1 1 0 0 1 1-1h3.5a1 1 0 0 1 1 1c0 1.25.2 2.45.57 3.57a1 1 0 0 1-.25 1z"/></svg>
      323-555-0142
    </li>
    <li class="contact-item">
      <svg class="contact-icon" viewBox="0 0 24 24"><path d="M8 1h8a2 2 0 0 1 2 2v18a2 2 0 0 1-2 2H8a2 2 0 0 1-2-2V3a2 2 0 0 1 2-2zm0 3v14h8V4zm4 15.5a1.2 1.2 0 1 0 0 2.4 1.2 1.2 0 0 0 0-2.4z"/></svg>
      310-555-0187
    </li>
    <li class="contact-item">
      <svg class="contact-icon" viewBox="0 0 24 24"><path d="M7 2h8l3 3v5H7zM3 11h18a1 1 0 0 1 1 1v9a1 1 0 0 1-1 1H3a1 1 0 0 1-1-1v-9a1 1 0 0 1 1-1zm3 3v2h3v-2zm5 0v2h3v-2zm5 0v2h3v-2zm-10 4v2h3v-2zm5 0v2h3v-2zm5 0v2h3v-2z"/></svg>
      323-555-0163
    </li>
    <li class="contact-item">
      <svg class="contact-icon" viewBox="0 0 24 24"><path d="M12 2a10 10 0 1 0 5 18.7l-1-1.7A8 8 0 1 1 20 12v1.2a1.8 1.8 0 0 1-3.6 0V7h-2v1a5 5 0 1 0 .6 7.3 3.8 3.8 0 0 0 7-2V12A10 10 0 0 0 12 2zm0 13a3 3 0 1 1 0-6 3 3 0 0 1 0 6z"/></svg>
      derek@drquillenterprises.com
    </li>
    <li class="contact-item">
      <svg class="contact-icon" viewBox="0 0 24 24"><path d="M12 2a10 10 0 1 0 0 20 10 10 0 0 0 0-20zm6.9 6h-2.9a15 15 0 0 0-1.4-3.6A8 8 0 0 1 18.9 8zM12 4a13 13 0 0 1 1.9 4h-3.8A13 13 0 0 1 12 4zM4.3 14a8 8 0 0 1 0-4h3.4a16 16 0 0 0 0 4zm.8 2h2.9a15 15 0 0 0 1.4 3.6A8 8 0 0 1 5.1 16zM8 8H5.1a8 8 0 0 1 4.3-3.6A15 15 0 0 0 8 8zm4 12a13 13 0 0 1-1.9-4h3.8A13 13 0 0 1 12 20zm2.3-6H9.7a14 14 0 0 1 0-4h4.6a14 14 0 0 1 0 4zm.3 5.6A15 15 0 0 0 16 16h2.9a8 8 0 0 1-4.3 3.6zM16.3 14a16 16 0 0 0 0-4h3.4a8 8 0 0 1 0 4z"/></svg>
      drquillenterprises.com
    </li>
  </ul>

  <svg class="footer-band" viewBox="0 0 1000 57" preserveAspectRatio="none">
    <defs>
      <linearGradient id="copper" x1="0" y1="0" x2="1" y2="0">
        <stop offset="0" stop-color="#b9693a"/>
        <stop offset=".45" stop-color="#f2b98f"/>
        <stop offset=".75" stop-color="#c97a45"/>
        <stop offset="1" stop-color="#a85a2c"/>
      </linearGradient>
    </defs>
    <rect x="0" y="0" width="1000" height="57" fill="url(#copper)"/>
    <polygon points="720,0 1000,0 1000,57 682,57" fill="#141414"/>
  </svg>
</div>
</body>
</html>
```